Looking for a modern, Professional business card design

We have a simple business card, but are looking for a more modern, professional look. A sample of the basic card is attached as well as the logo. We would also like to add that we offer:
Struggling with your finances?
- Learn to become debt free
- Discover the power of cash
- Control your money instead of it controlling you
Let us help you achieve a new level of financial freedom!
Also, we would like to have a "SPECIAL OFFER!: FREE 30 minute consultation"
Financial Planning

```html
<!DOCTYPE html>
<html lang="en">
<head>
<meta charset="utf-8">
<title>Steady Ledger Coaching – Business Card</title>
<link rel="stylesheet" href="https://fonts.googleapis.com/css2?family=Jost:wght@400;500&family=Russo+One&display=swap">
<style>
  :root {
    --green: #6cc531;
    --green-deep: #3a9a35;
    --ink: #111111;
    --black-card: #050505;
    --paper: #ffffff;
    --stage: #e9ebe8;
    --text-light: #f2f2f2;
  }
  * { box-sizing: border-box; margin: 0; padding: 0; }
  html, body { width: 1200px; height: 900px; overflow: hidden; }
  body {
    background: var(--stage);
    font-family: "Jost", sans-serif;
    position: relative;
  }
  .card {
    position: absolute;
    width: 640px;
    height: 366px;
    border-radius: 22px;
    overflow: hidden;
    box-shadow: 0 10px 30px rgba(0,0,0,0.18);
  }

  /* Front: message side */
  .card-front {
    left: 60px; top: 50px;
    background: var(--paper);
    color: var(--ink);
    text-align: center;
  }
  .brand-lockup {
    display: flex; align-items: center; justify-content: center; gap: 12px;
    margin-top: 62px;
  }
  .brand-dot { width: 22px; height: 22px; border-radius: 50%; background: var(--green); }
  .brand-name {
    font-family: "Russo One", sans-serif;
    font-size: 40px; color: var(--green); letter-spacing: 1px;
  }
  .pitch { margin-top: 44px; font-size: 19px; line-height: 1.32; }
  .pitch .accent { color: var(--green); font-weight: 500; }
  .pitch-heading { font-size: 20px; text-transform: uppercase; }

  /* Back: contact side */
  .card-back {
    left: 500px; top: 484px;
    background: var(--black-card);
    color: var(--text-light);
  }
  .back-brand {
    position: absolute; right: 40px; top: 46px; text-align: left;
  }
  .back-brand .brand-lockup { margin: 0; justify-content: flex-start; }
  .back-brand .brand-name { color: var(--paper); font-size: 38px; }
  .back-brand .brand-dot { background: var(--green); }
  .brand-subtitle {
    font-family: "Russo One", sans-serif;
    color: var(--green); font-size: 15px; margin: 2px 0 0 34px; text-transform: uppercase;
  }
  .brand-tagline { font-size: 10px; color: #cfcfcf; margin-left: 34px; }

  .contact { position: absolute; left: 36px; top: 158px; }
  .person-name {
    font-family: "Russo One", sans-serif;
    font-size: 28px; color: var(--green); text-transform: uppercase; line-height: 1;
  }
  .person-role {
    font-family: "Russo One", sans-serif;
    font-size: 14px; color: var(--paper); text-transform: uppercase; margin-top: 4px;
  }
  .contact-list { list-style: none; margin-top: 16px; }
  .contact-list li {
    display: flex; align-items: center; gap: 12px;
    font-size: 19px; line-height: 1.4;
  }
  .contact-list svg { width: 16px; height: 16px; flex: none; }
  .contact-list .web-accent { color: var(--green); }

  .offer-band {
    position: absolute; left: 0; right: 0; bottom: 0; height: 50px;
    background: var(--green-deep);
    border-top: 6px solid var(--black-card);
    box-shadow: 0 -2px 0 var(--green);
    display: flex; align-items: center; justify-content: center; gap: 10px;
    color: var(--paper);
  }
  .offer-label { font-family: "Russo One", sans-serif; font-size: 17px; text-transform: uppercase; }
  .offer-detail { font-size: 21px; text-transform: uppercase; letter-spacing: 0.5px; }
</style>
</head>
<body>

  <section class="card card-front">
    <div class="brand-lockup">
      <span class="brand-dot"></span>
      <span class="brand-name">STEADY LEDGER</span>
    </div>
    <div class="pitch">
      <p class="pitch-heading"><span class="accent">Struggling</span> with your <span class="accent">finances?</span></p>
      <p>Learn to become debt free</p>
      <p>Discover the power of cash</p>
      <p>Control your money instead of it controlling you</p>
      <p>Let us help you achieve a new level of financial <span class="accent">FREEDOM!</span></p>
    </div>
  </section>

  <section class="card card-back">
    <div class="back-brand">
      <div class="brand-lockup">
        <span class="brand-dot"></span>
        <span class="brand-name">STEADY LEDGER</span>
      </div>
      <p class="brand-subtitle">Financial Coaching</p>
      <p class="brand-tagline">Achieve a new level of personal freedom</p>
    </div>

    <div class="contact">
      <p class="person-name">Daniel R. Hayes</p>
      <p class="person-role">Personal Financial Coach</p>
      <ul class="contact-list">
        <li>
          <svg viewBox="0 0 16 16" aria-hidden="true"><rect x="4" y="1" width="8" height="14" rx="1.5" fill="none" stroke="#6cc531" stroke-width="1.5"/><circle cx="8" cy="12.3" r="0.9" fill="#6cc531"/></svg>
          (555) 014-2287
        </li>
        <li>
          <svg viewBox="0 0 16 16" aria-hidden="true"><rect x="1" y="3" width="14" height="10" rx="1" fill="none" stroke="#6cc531" stroke-width="1.5"/><path d="M1.5 3.8 8 9l6.5-5.2" fill="none" stroke="#6cc531" stroke-width="1.5"/></svg>
          daniel@steadyledgercoaching.com
        </li>
        <li>
          <svg viewBox="0 0 16 16" aria-hidden="true"><circle cx="8" cy="8" r="6.5" fill="none" stroke="#6cc531" stroke-width="1.4"/><ellipse cx="8" cy="8" rx="2.8" ry="6.5" fill="none" stroke="#6cc531" stroke-width="1.2"/><path d="M1.5 8h13" stroke="#6cc531" stroke-width="1.2"/></svg>
          <span>www.<span class="web-accent">steadyledgercoaching</span>.com</span>
        </li>
      </ul>
    </div>

    <div class="offer-band">
      <span class="offer-label">Special Offer! Free</span>
      <span class="offer-detail">30 Minute Consultation</span>
    </div>
  </section>

</body>
</html>
```